Fenlow Systems

Looking for a web site design to market our services/applications
We write and supply bespoke web applications for the offshore and construction industries
Our initial product is Tolv - rope access equipment management
Our buyers will be Rope Access companies via trade associations such as KOBEN and DULMO
we have a logo designed see it attached we would like to see crisp professional designs based around these colours and design
we will supply web copy later
looking for home, services, blog, contact us, order and a general template (privacy, site map, T&C) pages
Updates
This payment will be for the homepage only
We can discuss other options (pages) with the successful designer
Regards
Marcus
Industry/Entity Type
Construction
Look and feel
Each slider illustrates characteristics of the customer's brand and the style your logo design should communicate.

```html
<!DOCTYPE html>
<html lang="en">
<head>
<meta charset="utf-8">
<title>Fenlow Systems — Home</title>
<link href="https://fonts.googleapis.com/css2?family=Open+Sans:wght@400;600;700&display=swap" rel="stylesheet">
<style>
:root{
  --navy:#14237f;
  --brand-blue:#1a8fd8;
  --link-blue:#1b9ee0;
  --text:#6d6d6d;
  --muted:#8a8a8a;
  --band:#f3f3f3;
  --footer:#2b2b2b;
  --footer-text:#b9b9b9;
  --white:#ffffff;
}
*{margin:0;padding:0;box-sizing:border-box}
html,body{width:890px;height:1200px;overflow:hidden;background:var(--white)}
body{font-family:"Open Sans",Arial,sans-serif;color:var(--text);position:relative}
.abs{position:absolute}

/* header */
.brand-mark{left:74px;top:28px;width:53px;height:53px;border-radius:6px;background:linear-gradient(#f4f4f4,#dcdcdc)}
.brand-divider{left:138px;top:17px;width:1px;height:75px;background:#d5d5d5}
.brand-name{left:147px;top:34px;font-size:19px;line-height:22px;font-weight:600;color:var(--navy);letter-spacing:-.4px}
.call{right:75px;top:22px;font-size:14.5px;color:var(--link-blue);display:flex;align-items:center;gap:6px}
.call strong{color:var(--navy);font-weight:600;margin-left:4px}
.nav{top:68px;font-size:11.5px;color:var(--muted)}
.nav.active{color:var(--navy)}

/* hero */
.hero{left:0;top:112px;width:890px;height:344px;background:linear-gradient(115deg,#5d86a8 0%,#8fb3cf 35%,#6fa9bd 60%,#9fd3da 85%,#c6e4ea 100%)}
.slide-arrow{width:31px;height:38px;background:rgba(80,90,100,.6);display:flex;align-items:center;justify-content:center}
.hero-title{left:76px;top:348px;width:134px;height:50px;background:rgba(35,65,170,.85);color:#fff;font-size:38px;font-weight:600;line-height:50px;padding-left:10px}
.hero-sub{left:76px;top:402px;width:358px;height:31px;background:rgba(40,40,40,.82);color:#fff;font-size:17.5px;line-height:31px;padding-left:10px}

/* features */
.features{left:0;top:456px;width:890px;height:138px;background:var(--band)}
.feature-icon{width:56px;height:56px;border-radius:50%;background:var(--brand-blue);display:flex;align-items:center;justify-content:center}
.feature-title{font-size:14.5px;font-weight:600;color:var(--navy);top:493px}
.feature-text{font-size:9.3px;line-height:14px;color:var(--muted);top:514px;width:160px}

/* welcome */
.h2{font-size:19.5px;font-weight:600;color:var(--navy)}
.intro{left:76px;top:661px;width:515px;font-size:10.3px;line-height:17px}
.demo{left:76px;top:741px;width:282px;height:161px;background:linear-gradient(#2b2b2b,#1b1b1b);overflow:hidden}
.demo-label{left:0;width:282px;top:114px;text-align:center;font-size:30px;font-weight:700;color:#6f6f6f;letter-spacing:1px}
.checks{left:375px;top:746px;list-style:none;font-size:11.2px;color:var(--link-blue)}
.checks li{height:24.8px;display:flex;align-items:center;gap:7px}
.checks li.more{padding-left:18px}

/* blog */
.blog-img{left:623px;top:666px;width:193px;height:106px;background:radial-gradient(circle at 50% 45%,#5a5a5a,#2a2a2a 55%,#d8d8d8 100%)}
.post-title{left:623px;top:784px;font-size:12px;color:var(--link-blue)}
.post-text{left:623px;top:804px;width:195px;font-size:9.2px;line-height:14px;color:var(--muted)}
.post-meta{left:623px;top:884px;font-size:9.5px;color:#9a9a9a;display:flex;align-items:center;gap:14px}

/* cta */
.cta{left:0;top:946px;width:890px;height:122px;background:var(--band)}
.cta-text{left:0;width:890px;top:975px;text-align:center;font-size:16px;color:#555}
.cta-btn{left:383px;top:1004px;width:124px;height:34px;border-radius:3px;background:linear-gradient(#6a6a6a,#4a4a4a);color:#fff;font-size:15px;line-height:34px;text-align:center}

/* footer */
.footer{left:0;top:1068px;width:890px;height:132px;background:var(--footer)}
.footer-links{left:74px;top:1088px;width:742px;display:flex;justify-content:space-between;padding:0 20px;font-size:10.5px;color:var(--footer-text)}
.footer-rule{left:74px;top:1120px;width:742px;height:1px;background:#444}
.copyright{left:76px;top:1139px;font-size:10.5px;color:var(--footer-text)}
.social{top:1164px;width:22px;height:22px;border-radius:50%;background:#555;border:2px solid #1c1c1c}
.badge{background:#d9d9d9}
</style>
</head>
<body>

<header>
  <div class="abs brand-mark"></div>
  <div class="abs brand-divider"></div>
  <div class="abs brand-name">Fenlow<br>Systems</div>
  <div class="abs call">
    <svg width="15" height="15" viewBox="0 0 16 16"><circle cx="8" cy="8" r="7.2" fill="none" stroke="#1b9ee0" stroke-width="1.4"/><path d="M5.3 4.5l1.5-.3.8 2-1 .8c.5 1 1.2 1.7 2.2 2.2l.8-1 2 .8-.3 1.5c-3.2.2-6.2-2.8-6-6z" fill="#1b9ee0"/></svg>
    Call us <strong>555 014 2287</strong>
  </div>
  <nav>
    <span class="abs nav active" style="left:525px">Home</span>
    <span class="abs nav" style="left:583px">Services</span>
    <span class="abs nav" style="left:653px">Blog</span>
    <span class="abs nav" style="left:703px">Order</span>
    <span class="abs nav" style="left:761px">Contact us</span>
  </nav>
</header>

<section>
  <div class="abs hero" role="img" aria-label="Photo of two rope access technicians in orange vests and red helmets cleaning a glass building"></div>
  <div class="abs slide-arrow" style="left:6px;top:278px"><svg width="12" height="24" viewBox="0 0 12 24"><path d="M10 2L2 12l8 10" fill="none" stroke="#fff" stroke-width="1.3"/></svg></div>
  <div class="abs slide-arrow" style="left:860px;top:265px"><svg width="12" height="24" viewBox="0 0 12 24"><path d="M2 2l8 10-8 10" fill="none" stroke="#fff" stroke-width="1.3"/></svg></div>
  <div class="abs hero-title">TOLV</div>
  <div class="abs hero-sub">ROPE ACCESS EQUIPMENT MANAGEMENT</div>
</section>

<section>
  <div class="abs features"></div>
  <div class="abs feature-icon" style="left:79px;top:496px">
    <svg width="22" height="22" viewBox="0 0 22 22"><rect x="2" y="3" width="18" height="17" fill="none" stroke="#fff" stroke-width="1.6"/><rect x="2" y="3" width="18" height="4" fill="#fff"/><g fill="#fff"><rect x="5" y="9" width="3" height="2.5"/><rect x="9.5" y="9" width="3" height="2.5"/><rect x="14" y="9" width="3" height="2.5"/><rect x="5" y="13" width="3" height="2.5"/><rect x="9.5" y="13" width="3" height="2.5"/><rect x="14" y="13" width="3" height="2.5"/></g></svg>
  </div>
  <div class="abs feature-title" style="left:147px">SCHEDULING</div>
  <p class="abs feature-text" style="left:147px">Proin accumsan consectetur purus id rutrum. Duis tempus est ac finibus egestas.</p>

  <div class="abs feature-icon" style="left:337px;top:496px">
    <svg width="22" height="22" viewBox="0 0 22 22" fill="#fff"><rect x="8.5" y="2" width="5" height="4.5"/><rect x="2" y="15" width="5" height="4.5"/><rect x="8.5" y="15" width="5" height="4.5"/><rect x="15" y="15" width="5" height="4.5"/><path d="M10.3 6.5h1.4v4h6v4.5h-1.4v-3.1h-4.6v3.1h-1.4v-3.1H5.7v3.1H4.3v-4.5h6z"/></svg>
  </div>
  <div class="abs feature-title" style="left:405px">WORK MANAGEMENT</div>
  <p class="abs feature-text" style="left:405px">Proin accumsan consectetur purus id rutrum. Duis tempus est ac finibus egestas.</p>

  <div class="abs feature-icon" style="left:594px;top:496px">
    <svg width="20" height="22" viewBox="0 0 20 22"><path d="M3 1h10l5 5v15H3z" fill="#fff"/><g stroke="#1a8fd8" stroke-width="1.2"><path d="M6 9h9M6 12h9M6 15h9"/></g></svg>
  </div>
  <div class="abs feature-title" style="left:662px">DATA STORAGE</div>
  <p class="abs feature-text" style="left:662px">Proin accumsan consectetur purus id rutrum. Duis tempus est ac finibus egestas.</p>
</section>

<main>
  <h2 class="abs h2" style="left:76px;top:628px">Welcome to Fenlow Systems</h2>
  <p class="abs intro">Fusce convallis consectetur velit, sit amet laoreet eros. Pellentesque scelerisque turpis finibus elit viverra, ac dapibus arcu tristique. Cras ut lorem et sem pretium pellentesque. Nulla sed arcu a erat faucibus malesuada. Curabitur nibh tellus, pretium at dolor vel, placerat volutpat enim. Donec tristique tincidunt nibh, ut ornare ante egestas ut. Morbi consectetur dictum nibh at consequat.</p>

  <div class="abs demo" role="img" aria-label="Screenshot of the Tolv application dashboard">
    <svg class="abs" style="left:111px;top:51px" width="60" height="60" viewBox="0 0 60 60"><circle cx="30" cy="30" r="27" fill="rgba(0,0,0,.35)" stroke="#fff" stroke-width="4"/><path d="M23 17l20 13-20 13z" fill="#fff"/></svg>
    <div class="abs demo-label">DEMO</div>
  </div>

  <ul class="abs checks">
    <li><svg width="11" height="9" viewBox="0 0 11 9"><path d="M1 4.5l3 3L10 1" fill="none" stroke="#1b9ee0" stroke-width="1.6"/></svg>Curabitur placerat malesuada nulla</li>
    <li><svg width="11" height="9" viewBox="0 0 11 9"><path d="M1 4.5l3 3L10 1" fill="none" stroke="#1b9ee0" stroke-width="1.6"/></svg>Etiam non pretium eros</li>
    <li><svg width="11" height="9" viewBox="0 0 11 9"><path d="M1 4.5l3 3L10 1" fill="none" stroke="#1b9ee0" stroke-width="1.6"/></svg>Praesent aliquam urna massa efficitur</li>
    <li><svg width="11" height="9" viewBox="0 0 11 9"><path d="M1 4.5l3 3L10 1" fill="none" stroke="#1b9ee0" stroke-width="1.6"/></svg>Suspendisse ut ex laoreet dui</li>
    <li class="more">...and More</li>
  </ul>

  <aside>
    <h2 class="abs h2" style="left:623px;top:628px">Blog</h2>
    <svg class="abs" style="left:797px;top:634px" width="19" height="19" viewBox="0 0 19 19"><circle cx="9.5" cy="9.5" r="8.5" fill="none" stroke="#888" stroke-width="1.4"/><path d="M5 9.5h8M10 6l3.5 3.5L10 13" fill="none" stroke="#888" stroke-width="1.4"/></svg>
    <div class="abs blog-img" role="img" aria-label="Photo of a worker in a yellow helmet cleaning the inside of a large pipe"></div>
    <div class="abs post-title">Donec tellus erat accumsan</div>
    <p class="abs post-text">Nulla facilisi. Aenean viverra massa et libero volutpat, et eleifend sapien tristique. Ves tibulum ante ipsum primis in faucibus orci luctus et ultrices posuere cubilia sed inter dum ante semper.</p>
    <div class="abs post-meta">
      <span>Sep 2, 2014</span>
      <svg width="11" height="9" viewBox="0 0 11 9"><path d="M0 2h3l4 5h3M0 7h3l4-5h3" fill="none" stroke="#8a8a8a" stroke-width="1.2"/></svg>
      <svg width="10" height="9" viewBox="0 0 10 9"><path d="M0 0h10v6H4L1 9V6H0z" fill="#8a8a8a"/></svg>
    </div>
  </aside>
</main>

<section>
  <div class="abs cta"></div>
  <p class="abs cta-text">Curabitur placerat malesuada nulla ac ultricies lobortis tempor lectus</p>
  <div class="abs cta-btn">ORDER NOW</div>
</section>

<footer>
  <div class="abs footer"></div>
  <div class="abs footer-links">
    <span>• Home</span><span>• Services</span><span>• Blog</span><span>• Order</span><span>• Contact us</span><span>• Privacy Policy</span><span>• Terms and Conditons</span><span>• Sitemap</span>
  </div>
  <div class="abs footer-rule"></div>
  <div class="abs copyright">Copyright &copy; 2014 Fenlow Systems.&nbsp;&nbsp; All rights reserved.</div>
  <div class="abs social" style="left:76px" aria-label="Social profile"></div>
  <div class="abs social" style="left:106px" aria-label="Social profile"></div>
  <div class="abs social" style="left:135px" aria-label="Social profile"></div>
  <div class="abs social" style="left:164px" aria-label="Social profile"></div>
  <div class="abs badge" style="left:650px;top:1146px;width:68px;height:38px;border-radius:50%" aria-label="KOBEN member badge"></div>
  <div class="abs badge" style="left:729px;top:1146px;width:87px;height:38px;border-radius:3px" aria-label="DULMO member badge"></div>
</footer>

</body>
</html>
```